Brivano Rebranded Website boutique fitness studio

Looking for a simple, easy to navigate, aesthetically pleasing update of our rebranded website

Target Market(s)

Stay at home moms, discretionary income, fitness and wellness

Coding

Coded - Design and coding required

Number of Pages Required

1 page

Font styles to use
Sans Serif

Colors
0054AA
0677BA
7BADD7
CADEEF
E8F1F8

Requirements
Must have
• Instagram feed linked, "as seen in" banner, spot for studio video at a later date

```html
<!DOCTYPE html>
<html lang="en">
<head>
<meta charset="UTF-8">
<title>Brivano — Strength Without Intimidation</title>
<link href="https://fonts.googleapis.com/css2?family=Work+Sans:wght@400;500;600;700;800&family=Plus+Jakarta+Sans:wght@300;400;500;600&display=swap" rel="stylesheet">
<style>
  :root {
    --navy: #0d1f33;
    --maroon: #560006;
    --cream: #f8f4ef;
    --chip-bg: #f3eee8;
    --chip-border: #d9d3cc;
    --text-soft: #3a3a3a;
    --white: #ffffff;
  }
  * { margin: 0; padding: 0; box-sizing: border-box; }
  html, body { width: 1200px; height: 679px; overflow: hidden; }
  body {
    position: relative;
    background: var(--cream);
    font-family: "Work Sans", sans-serif;
    color: var(--navy);
  }
  .hero-photo {
    position: absolute; inset: 0;
    background:
      radial-gradient(ellipse at 82% 45%, #c9a888 0%, #d8bfa5 30%, rgba(230,214,196,0) 65%),
      linear-gradient(90deg, #f8f4ef 0%, #f6f0e8 38%, #eadbc9 58%, #d9bfa2 78%, #c8a585 100%);
  }
  .hero-fade {
    position: absolute; inset: 0;
    background: linear-gradient(90deg, rgba(248,244,239,0.96) 0%, rgba(248,244,239,0.85) 40%, rgba(248,244,239,0) 70%);
  }
  .site-header {
    position: absolute; top: 0; left: 0; width: 100%; height: 70px;
  }
  .brand {
    position: absolute; left: 102px; top: 24px;
    display: flex; align-items: center; gap: 5px;
    font-weight: 700; font-size: 13px; color: var(--maroon);
  }
  .brand-dot { width: 8px; height: 8px; border-radius: 50%; background: var(--maroon); }
  .main-nav {
    position: absolute; top: 28px; left: 301px;
    display: flex; gap: 29px;
    font-size: 10.5px; font-weight: 600; color: var(--navy);
  }
  .btn {
    position: absolute; display: flex; align-items: center; justify-content: center;
    border-radius: 40px; font-size: 10px; font-weight: 600; letter-spacing: 2px;
    text-transform: uppercase;
  }
  .btn-solid { background: var(--navy); color: var(--white); }
  .btn-outline { border: 1.5px solid var(--navy); color: var(--navy); background: transparent; }
  .btn-book-now { left: 980px; top: 15px; width: 123px; height: 37px; }
  .eyebrow {
    position: absolute; font-size: 9.5px; font-weight: 600; letter-spacing: 2.2px;
    color: var(--maroon); text-transform: uppercase;
  }
  .hero-eyebrow { left: 97px; top: 119px; }
  .hero-title {
    position: absolute; left: 95px; top: 142px;
    font-size: 75px; font-weight: 800; line-height: 77px; letter-spacing: 1.5px;
  }
  .hero-title .accent { color: var(--maroon); }
  .hero-lede {
    position: absolute; left: 97px; top: 398px;
    font-family: "Plus Jakarta Sans", sans-serif; font-size: 17px; line-height: 27px;
    color: var(--text-soft); font-weight: 300;
  }
  .hero-lede strong { font-weight: 500; color: #1d1d1d; }
  .btn-first { left: 97px; top: 484px; width: 209px; height: 37px; }
  .btn-schedule { left: 319px; top: 480px; width: 208px; height: 45px; }
  .chip {
    position: absolute; height: 27px; border-radius: 20px;
    border: 1px solid var(--chip-border); background: var(--chip-bg);
    display: flex; align-items: center; gap: 6px; padding-left: 12px;
    font-size: 10px; font-weight: 600; color: var(--navy);
  }
  .chip svg { width: 12px; height: 12px; }
  .scroll-cue {
    position: absolute; left: 545px; top: 610px; width: 110px; text-align: center;
    font-size: 8.5px; letter-spacing: 2px; color: #555;
  }
  .scroll-cue .line { width: 1px; height: 28px; background: #999; margin: 0 auto 11px; }
  .offer-card {
    position: absolute; left: 911px; top: 456px; width: 253px; height: 187px;
    background: var(--white); border-radius: 22px;
    box-shadow: 0 8px 24px rgba(0,0,0,0.08);
  }
  .offer-card .eyebrow { left: 30px; top: 29px; font-size: 8.5px; }
  .offer-title { position: absolute; left: 30px; top: 49px; font-size: 14px; font-weight: 500; }
  .offer-text {
    position: absolute; left: 30px; top: 76px; width: 200px;
    font-family: "Plus Jakarta Sans", sans-serif; font-size: 13.5px; line-height: 24px;
    font-weight: 300; color: var(--text-soft);
  }
  .offer-card .btn { left: 30px; top: 135px; width: 195px; height: 27px; font-size: 9.5px; }
</style>
</head>
<body>
  <div class="hero-photo" role="img" aria-label="Bright studio photo of an instructor guiding a smiling client on a reformer machine, with plants and sunlight"></div>
  <div class="hero-fade"></div>

  <header class="site-header">
    <div class="brand"><span class="brand-dot"></span>Brivano</div>
    <nav class="main-nav">
      <span>Home</span><span>New Here</span><span>Schedule</span><span>Memberships</span>
      <span>Studios</span><span>Life at Brivano</span><span>Contact</span>
    </nav>
    <a class="btn btn-solid btn-book-now">Book Now</a>
  </header>

  <p class="eyebrow hero-eyebrow">Elevated Strength Begins Here</p>
  <h1 class="hero-title">Strength<br>Without<br><span class="accent">Intimidation.</span></h1>
  <p class="hero-lede">Luxury Lumora classes designed for every body.<br><strong>Build strength. Move with confidence. Feel your best.</strong></p>

  <a class="btn btn-solid btn-first">Book Your First Class</a>
  <a class="btn btn-outline btn-schedule">View Schedule &amp; Book</a>

  <div class="chip" style="left:97px;top:557px;width:127px;">
    <svg viewBox="0 0 12 12"><path d="M6 .8l1.6 3.3 3.6.5-2.6 2.5.6 3.6L6 9l-3.2 1.7.6-3.6L.8 4.6l3.6-.5z" fill="#f2b705"/></svg>5.0 Vantly Rating
  </div>
  <div class="chip" style="left:234px;top:557px;width:133px;">
    <svg viewBox="0 0 12 12"><path d="M6 1a3 3 0 0 1 3 3c0 2.2-3 7-3 7S3 6.2 3 4a3 3 0 0 1 3-3z" fill="#d8262e"/><circle cx="6" cy="4" r="1" fill="#fff"/></svg>2 Studio Locations
  </div>
  <div class="chip" style="left:377px;top:557px;width:128px;">
    <svg viewBox="0 0 12 12"><circle cx="4" cy="4" r="2" fill="#3a6ea5"/><circle cx="8.5" cy="4" r="2" fill="#3a6ea5"/><path d="M0.5 11a3.5 3.5 0 0 1 7 0zM5 11a3.5 3.5 0 0 1 7 0z" fill="#3a6ea5"/></svg>Beginner Friendly
  </div>
  <div class="chip" style="left:97px;top:595px;width:125px;">
    <svg viewBox="0 0 12 12"><circle cx="6" cy="6.8" r="4.3" fill="none" stroke="#555" stroke-width="1"/><path d="M6 6.8V4.3M5 1.2h2" stroke="#555" stroke-width="1"/></svg>45 Minute Classes
  </div>

  <div class="scroll-cue"><div class="line"></div>SCROLL TO EXPLORE</div>

  <aside class="offer-card">
    <p class="eyebrow">New Client Offer</p>
    <h2 class="offer-title">Try Your First Class</h2>
    <p class="offer-text">14 Days Unlimited Access for $89</p>
    <a class="btn btn-solid">Book Reservation</a>
  </aside>
</body>
</html>
```